Business Card Design Project

I require a business card with the following information on them for various different people;
name
m:
f:
e:
I have a logo already and will attached that. We are in the construction industry. I require something clean and simple but eye catching at the same time. You can use another colour with our logo if you like and you can style the logo as well if you wish. I am open.
Also it needs to be front and back design.
Industry/Entity Type
Construction
Requirements
Must have
- Logo, name, mobile, fax and email address.
Front and back design

```html
<!DOCTYPE html>
<html lang="en">
<head>
<meta charset="utf-8">
<title>Stonebridge Developments – Business Card</title>
<link rel="stylesheet" href="https://fonts.googleapis.com/css2?family=Open+Sans:wght@400;700&display=swap">
<style>
  :root {
    --backdrop: #ebe8e1;
    --card-white: #ffffff;
    --green-deep: #55ab25;
    --green-mid: #7cc43a;
    --green-light: #c4ef62;
    --charcoal-deep: #000000;
    --charcoal-mid: #2e2e2e;
    --gray-mid: #4f4f4f;
    --gray-light: #6a6a6a;
    --ink: #111111;
    --brand-ink: #3f3f3f;
  }
  html, body {
    margin: 0;
    padding: 0;
    width: 1200px;
    height: 686px;
    overflow: hidden;
    background: var(--backdrop);
    font-family: "Open Sans", Arial, sans-serif;
  }
  .canvas {
    position: relative;
    width: 1200px;
    height: 686px;
  }
  .card {
    position: absolute;
    width: 507px;
    height: 289px;
    display: block;
    background: var(--card-white);
    box-shadow: 0 1px 3px rgba(0,0,0,0.25);
  }
  .card--front { left: 65px; top: 148px; }
  .card--back  { left: 608px; top: 243px; }
  .brand-name,
  .brand-tagline {
    font-family: "Open Sans", Arial, sans-serif;
    font-weight: 400;
    fill: var(--brand-ink);
  }
  .brand-name { font-size: 28px; }
  .brand-tagline { font-size: 11px; letter-spacing: 4px; }
  .card--back .brand-name { font-size: 36px; }
  .card--back .brand-tagline { font-size: 14px; letter-spacing: 5px; }
  .holder-name {
    font-family: "Open Sans", Arial, sans-serif;
    font-weight: 700;
    font-size: 19px;
    fill: var(--ink);
  }
  .contact-line {
    font-family: "Open Sans", Arial, sans-serif;
    font-weight: 400;
    font-size: 14px;
    fill: var(--ink);
  }
  .contact-icon { fill: var(--ink); }
</style>
</head>
<body>
<main class="canvas">

  <svg class="card card--front" viewBox="0 0 591 337" aria-label="Business card front">
    <defs>
      <linearGradient id="front-band-deep" x1="0" y1="0" x2="1" y2="0">
        <stop offset="0" stop-color="var(--green-deep)"/>
        <stop offset="0.6" stop-color="var(--green-deep)"/>
        <stop offset="1" stop-color="var(--green-mid)"/>
      </linearGradient>
      <linearGradient id="front-band-light" x1="0" y1="0.6" x2="0.7" y2="0.2">
        <stop offset="0" stop-color="var(--green-deep)"/>
        <stop offset="0.55" stop-color="var(--green-light)"/>
        <stop offset="1" stop-color="var(--green-light)"/>
      </linearGradient>
    </defs>
    <rect class="card-surface" width="591" height="337" fill="var(--card-white)"/>
    <polygon class="band band--lower" points="0,202 154,117 271,337 0,337" fill="url(#front-band-deep)"/>
    <polygon class="band band--upper" points="232,70 354,0 591,0 591,145 351,280" fill="url(#front-band-light)"/>

    <g class="brand-mark" transform="translate(180,104) rotate(57)">
      <rect x="0" y="-17" width="14" height="14" fill="var(--green-deep)"/>
      <text class="brand-name" x="22" y="0">Stonebridge</text>
      <text class="brand-tagline" x="24" y="16">DEVELOPMENTS</text>
    </g>

    <g class="contact-block" transform="translate(302,127) rotate(-29)">
      <text class="holder-name" x="0" y="0">Your Name</text>
      <g transform="translate(20,28)">
        <path class="contact-icon" d="M1,-9 c2,-1 3,0 3,1 l0,2 c0,1 -1,1 -2,1 c0,2 2,4 4,4 c0,-1 0,-2 1,-2 l2,0 c1,0 2,1 1,3 c-2,2 -6,1 -9,-3 c-2,-3 -2,-5 0,-6 z"/>
        <text class="contact-line" x="14" y="0">123-456-7890</text>
      </g>
      <g transform="translate(20,48)">
        <rect class="contact-icon" x="0" y="-9" width="11" height="9" rx="1"/>
        <rect x="2" y="-12" width="7" height="4" fill="var(--ink)"/>
        <text class="contact-line" x="14" y="0">123-456-7890</text>
      </g>
      <g transform="translate(20,68)">
        <rect class="contact-icon" x="0" y="-8" width="11" height="8"/>
        <polyline points="0,-8 5.5,-3.5 11,-8" fill="none" stroke="var(--card-white)" stroke-width="1"/>
        <text class="contact-line" x="18" y="0">name@website.com</text>
      </g>
    </g>
  </svg>

  <svg class="card card--back" viewBox="0 0 591 337" aria-label="Business card back">
    <defs>
      <linearGradient id="back-band-deep" x1="0" y1="0.3" x2="1" y2="0">
        <stop offset="0" stop-color="var(--charcoal-deep)"/>
        <stop offset="1" stop-color="var(--charcoal-mid)"/>
      </linearGradient>
      <linearGradient id="back-band-light" x1="0" y1="0.6" x2="0.8" y2="0.2">
        <stop offset="0" stop-color="var(--gray-mid)"/>
        <stop offset="0.6" stop-color="var(--gray-light)"/>
        <stop offset="1" stop-color="var(--gray-mid)"/>
      </linearGradient>
    </defs>
    <rect class="card-surface" width="591" height="337" fill="var(--card-white)"/>
    <polygon class="band band--lower" points="0,222 203,107 329,317 289,337 0,337" fill="url(#back-band-deep)"/>
    <polygon class="band band--upper" points="322,39 391,0 591,0 591,163 449,244" fill="url(#back-band-light)"/>

    <g class="brand-mark" transform="translate(226,52) rotate(57)">
      <rect x="0" y="-22" width="18" height="18" fill="var(--green-deep)"/>
      <text class="brand-name" x="28" y="0">Stonebridge</text>
      <text class="brand-tagline" x="30" y="20">DEVELOPMENTS</text>
    </g>
  </svg>

</main>
</body>
</html>
```